National Mission Critical Construction Contractor needs Stationery Design to make a bold statement

We are a small commercial construction company, working primarily in mission critical facilities across the U.S.. We have exciting corporate changes going an and a new logo and office space so we need new stationery. The final design should incorporate our new logo and invoke a fresh, high-tech feel while looking simple and modern.

Industry/Entity Type

Construction

Contact Information for Business Card

We are required to list our state licensing qualifications on the back of our card.

Font styles to use
Sans Serif

Requirements
Must have
• We need to have a design for second page of stationery, envelopes both standard and with a window and for a 3 x 4 notepad.

```html
<!DOCTYPE html>
<html lang="en">
<head>
<meta charset="utf-8">
<title>Halden Peak – Business Card</title>
<link rel="stylesheet" href="https://fonts.googleapis.com/css2?family=Source+Sans+3:wght@400;600&display=swap">
<style>
  :root {
    --stage: #3a3a3a;
    --paper: #f7f7f7;
    --brand-blue: #1565b0;
    --brand-mid: #2a73c2;
    --brand-sky: #3aa0dc;
    --brand-green: #8bc34a;
    --ink: #4a4a4a;
    --white: #ffffff;
    --back-light: #f4f7fa;
    --back-tint: #e3edf5;
  }
  * { margin: 0; padding: 0; box-sizing: border-box; }
  html, body { width: 1200px; height: 750px; overflow: hidden; }
  body {
    background: var(--stage);
    font-family: "Source Sans 3", sans-serif;
    position: relative;
  }
  .card {
    position: absolute;
    top: 228px;
    width: 461px;
    height: 262px;
    overflow: hidden;
  }
  .card-front { left: 124px; background: var(--paper); }
  .card-back { left: 618px; }
  .card-shapes { position: absolute; inset: 0; }

  .brand {
    position: absolute;
    left: 25px;
    top: 26px;
    display: flex;
    align-items: center;
    gap: 12px;
  }
  .brand-dot {
    width: 53px; height: 53px;
    border-radius: 50%;
    border: 3px solid var(--brand-blue);
  }
  .brand-name {
    color: var(--brand-blue);
    font-size: 22px;
    font-weight: 400;
    letter-spacing: 0.5px;
  }

  .contact-list {
    position: absolute;
    left: 26px;
    top: 157px;
    list-style: none;
    color: var(--white);
    font-size: 13px;
    line-height: 17.6px;
  }
  .contact-list li { display: flex; align-items: center; gap: 8px; }
  .contact-list svg { width: 12px; height: 12px; fill: var(--white); flex: none; }

  .person {
    position: absolute;
    right: 24px;
    top: 137px;
    text-align: right;
    color: var(--white);
  }
  .person-name { font-size: 18px; font-weight: 600; line-height: 22px; }
  .person-role { font-size: 13px; line-height: 16px; }

  .address {
    position: absolute;
    right: 24px;
    top: 210px;
    text-align: right;
    color: var(--white);
    font-size: 13px;
    line-height: 17px;
    font-style: normal;
  }

  .back-field {
    position: absolute;
    inset: 0;
    background: linear-gradient(135deg, var(--back-tint) 0%, var(--back-light) 55%, var(--back-tint) 100%);
  }
  .back-name {
    position: absolute;
    left: 292px;
    width: 160px;
    top: 183px;
    text-align: center;
    font-size: 17px;
    line-height: 22px;
  }
  .back-web {
    position: absolute;
    left: 292px;
    width: 160px;
    top: 222px;
    text-align: center;
    color: var(--ink);
    font-size: 13px;
    line-height: 17px;
  }
</style>
</head>
<body>

  <section class="card card-front" aria-label="Business card front">
    <svg class="card-shapes" viewBox="0 0 461 262" aria-hidden="true">
      <polygon points="0,142 240,142 266,114 461,114 461,262 0,262" fill="var(--brand-blue)"/>
      <polygon points="0,134 83,134 79,142 0,142" fill="var(--brand-green)"/>
      <polygon points="86,134 165,134 161,142 82,142" fill="var(--brand-sky)"/>
      <polygon points="168,134 247,134 243,142 164,142" fill="var(--brand-mid)"/>
    </svg>

    <div class="brand">
      <span class="brand-dot"></span>
      <span class="brand-name">HALDEN PEAK</span>
    </div>

    <ul class="contact-list">
      <li><svg viewBox="0 0 24 24"><path d="M6.6 10.8a15 15 0 0 0 6.6 6.6l2.2-2.2c.3-.3.7-.4 1-.2 1.1.4 2.3.6 3.6.6.6 0 1 .4 1 1V20c0 .6-.4 1-1 1A17 17 0 0 1 3 4c0-.6.4-1 1-1h3.5c.6 0 1 .4 1 1 0 1.3.2 2.5.6 3.6.1.3 0 .7-.2 1z"/></svg>555 201 4478</li>
      <li><svg viewBox="0 0 24 24"><path d="M7 1h10a2 2 0 0 1 2 2v18a2 2 0 0 1-2 2H7a2 2 0 0 1-2-2V3a2 2 0 0 1 2-2zm0 3v14h10V4z"/></svg>555 309 7612</li>
      <li><svg viewBox="0 0 24 24"><path d="M6 2h12v5H6zM3 8h18a2 2 0 0 1 2 2v7h-4v5H5v-5H1v-7a2 2 0 0 1 2-2zm4 8v4h10v-4z"/></svg>555 417 2085</li>
      <li><svg viewBox="0 0 24 24"><path d="M2 5h20v14H2zm2 2v.5l8 5 8-5V7z"/></svg>office@haldenpeak.com</li>
      <li><svg viewBox="0 0 24 24"><path d="M12 2a10 10 0 1 0 0 20 10 10 0 0 0 0-20zm-1 17.9A8 8 0 0 1 4.1 11H8c0 3 1 6 3 8.9zM8 9H4.1A8 8 0 0 1 11 4.1C9 6.9 8 8 8 9zm5 10.9c2-2.9 3-5.9 3-8.9h3.9a8 8 0 0 1-6.9 8.9zM16 9c0-1-1-2.1-3-4.9A8 8 0 0 1 19.9 9z"/></svg>www.haldenpeak.com</li>
    </ul>

    <div class="person">
      <p class="person-name">MARCUS ELLERY</p>
      <p class="person-role">CEO/Founder</p>
    </div>

    <address class="address">
      1420 Birchwood Court<br>Fairbanks, Alaska 99701
    </address>
  </section>

  <section class="card card-back" aria-label="Business card back">
    <div class="back-field" role="img" aria-label="Soft pale blue background where the repeating brand pattern belongs"></div>
    <span class="brand-name back-name">HALDEN PEAK</span>
    <span class="back-web">www.haldenpeak.com</span>
  </section>

</body>
</html>
```